QVN MOONLIT GLOW Party

Hi,
Want to design a flyer for a party.

I have attached a design I would like you to work from and just add in the correct text:

QVN Events presents

November 2013

MOONLIT GLOW
PARTY

DJ COPPER WHISK
VENUE: TBA

DOORS OPEN 8PM

ENTRY STRICTLY OVER 18'S.

DRESS CODE: SMART CASUAL SULTRY SEXY SPRING THREADS

COST: $60 PER HEAD, includes champagne, beer & wine and canapes.

Tickets from www.quillvanenest.example.com.au or 0499 371 582.

```html
<!DOCTYPE html>
<html lang="en">
<head>
<meta charset="utf-8">
<title>QVN Events – Moonlit Glow Party</title>
<link rel="stylesheet" href="https://fonts.googleapis.com/css2?family=Michroma&family=Krona+One&family=Saira:wght@500;600;700&display=swap">
<style>
  :root {
    --ink: #07060b;
    --white: #f4f4f8;
    --silver-hi: #ffffff;
    --silver-mid: #c9cfdb;
    --silver-lo: #7e8796;
    --magenta: #d0318f;
    --rule: #b0307f;
  }
  * { margin: 0; padding: 0; box-sizing: border-box; }
  html, body { width: 866px; height: 1200px; overflow: hidden; background: var(--ink); }
  .flyer {
    position: relative; width: 866px; height: 1200px; overflow: hidden;
    background:
      radial-gradient(ellipse 70% 45% at 50% 40%, #1b1433 0%, transparent 70%),
      var(--ink);
    color: var(--white);
    font-family: "Saira", "Arial", sans-serif;
  }
  .foil-band {
    position: absolute; left: 0; width: 100%; height: 16px;
    background: linear-gradient(90deg, var(--silver-lo), var(--silver-mid) 20%, var(--silver-hi) 50%, var(--silver-mid) 80%, #4f7f88);
  }
  .foil-band--top { top: 0; }
  .foil-band--bottom { bottom: 0; height: 18px; }
  .center { position: absolute; left: 0; width: 100%; text-align: center; }
  .presenter { top: 50px; font-family: "Michroma", sans-serif; font-size: 23px; letter-spacing: 1px; }
  .presenter strong { font-family: "Krona One", sans-serif; font-weight: 400; }
  .presenter-rule {
    position: absolute; top: 93px; left: 318px; width: 230px; height: 2px;
    background: linear-gradient(90deg, transparent, var(--silver-mid), transparent);
  }
  .date { top: 102px; font-family: "Krona One", sans-serif; font-size: 28px; color: var(--magenta); letter-spacing: 2px; }
  .hero-art { position: absolute; top: 145px; left: 0; width: 866px; height: 620px; }
  .title-main {
    top: 632px; font-family: "Krona One", sans-serif; font-size: 80px; line-height: 1;
    letter-spacing: 1px;
    background: linear-gradient(180deg, var(--silver-hi) 0%, var(--silver-mid) 55%, #8e97a8 100%);
    -webkit-background-clip: text; background-clip: text; color: transparent;
  }
  .title-sub {
    top: 734px; font-family: "Michroma", sans-serif; font-size: 50px; line-height: 1;
    letter-spacing: 2px; color: var(--silver-mid);
  }
  .dj { top: 808px; font-family: "Michroma", sans-serif; font-size: 31px; color: var(--magenta); }
  .venue { top: 860px; font-weight: 700; font-size: 26px; color: #e3e3ea; letter-spacing: 1px; }
  .doors { top: 896px; font-weight: 600; font-size: 21px; color: #e3e3ea; letter-spacing: 1px; }
  .venue-rule { position: absolute; top: 934px; left: 141px; width: 583px; height: 1px; background: var(--rule); }
  .age { top: 946px; font-family: "Michroma", sans-serif; font-size: 23px; letter-spacing: 2px; }
  .details { position: absolute; top: 996px; left: 0; width: 100%; height: 92px; }
  .details-col { position: absolute; top: 0; font-weight: 600; font-size: 19px; line-height: 24px; }
  .details-col--dress { right: 459px; text-align: right; }
  .details-col--cost { left: 457px; }
  .details-head { height: 26px; }
  .details-label { color: var(--magenta); font-weight: 600; }
  .details-text { margin-top: 12px; }
  .details-price { color: var(--white); font-size: 22px; }
  .details-divider { position: absolute; left: 433px; top: 3px; width: 2px; height: 86px; background: var(--rule); }
  .tickets { position: absolute; top: 1098px; left: 0; width: 100%; height: 30px; }
  .tickets-rule { position: absolute; top: 16px; height: 1px; background: var(--rule); }
  .tickets-rule--left { left: 42px; width: 300px; }
  .tickets-rule--right { left: 526px; width: 300px; }
  .tickets-label { position: absolute; left: 0; width: 100%; text-align: center; font-weight: 600; font-size: 24px; color: var(--magenta); }
  .contact-phone { position: absolute; top: 1130px; left: 51px; font-weight: 600; font-size: 30px; }
  .contact-web { position: absolute; top: 1136px; right: 41px; font-weight: 600; font-size: 23px; }
</style>
</head>
<body>
<main class="flyer">
  <div class="foil-band foil-band--top"></div>

  <p class="center presenter">QVN EVENTS <strong>PRESENTS</strong></p>
  <div class="presenter-rule"></div>
  <p class="center date">NOVEMBER 2013</p>

  <svg class="hero-art" viewBox="0 0 866 620" role="img" aria-label="Neon-lit DJ in headphones among glowing rings, speaker shapes and champagne bottles">
    <defs>
      <radialGradient id="heroGlow" cx="50%" cy="45%" r="60%">
        <stop offset="0%" stop-color="#3b3a8a"/>
        <stop offset="35%" stop-color="#2a1f5e"/>
        <stop offset="65%" stop-color="#1a0f2e"/>
        <stop offset="100%" stop-color="#07060b" stop-opacity="0"/>
      </radialGradient>
      <radialGradient id="heroAccent" cx="30%" cy="60%" r="40%">
        <stop offset="0%" stop-color="#b0308f" stop-opacity="0.35"/>
        <stop offset="100%" stop-color="#b0308f" stop-opacity="0"/>
      </radialGradient>
    </defs>
    <rect width="866" height="620" fill="url(#heroGlow)"/>
    <rect width="866" height="620" fill="url(#heroAccent)"/>
  </svg>

  <h1 class="center title-main">MOONLIT</h1>
  <p class="center title-sub">GLOW PARTY</p>

  <p class="center dj">DJ COPPER WHISK</p>
  <p class="center venue">VENUE: TBA</p>
  <p class="center doors">DOORS OPEN 8PM</p>
  <div class="venue-rule"></div>
  <p class="center age">ENTRY STRICTLY OVER 18'S.</p>

  <section class="details">
    <div class="details-col details-col--dress">
      <p class="details-head"><span class="details-label">DRESS CODE:</span></p>
      <p class="details-text">SMART CASUAL SULTRY<br>SEXY SPRING THREADS</p>
    </div>
    <div class="details-divider"></div>
    <div class="details-col details-col--cost">
      <p class="details-head"><span class="details-label">COST:</span> <span class="details-price">$60 PER HEAD</span></p>
      <p class="details-text">INCLUDES CHAMPAGNE,<br>BEER &amp; WINE AND CANAPES.</p>
    </div>
  </section>

  <div class="tickets">
    <div class="tickets-rule tickets-rule--left"></div>
    <p class="tickets-label">Tickets from:</p>
    <div class="tickets-rule tickets-rule--right"></div>
  </div>
  <p class="contact-phone">ph: 0499 371 582</p>
  <p class="contact-web">www.QUILLVANENEST.example.com.au</p>

  <div class="foil-band foil-band--bottom"></div>
</main>
</body>
</html>
```